Business Postcard Design for Personal Training Company

Need a postcard design for my company called "Copperleaf Studio" Colors are Navy Blue, Blue, Grey and White.

On the front I want there to be pictures and it to feature a box that says "Free Consultation + 50% off your first session!"

And somehow to feature the following phrases " Lose Weight. Gain Muscle."
"Customized Personal training using Q-Pulse, the latest technology in fitness. Reach your fitness goals in just two 25-min sessions per week"

Also want featured the following phrases (maybe on back):

"up to 18 times more effective than a conventional gym workout"

I need the back of the postcard to have all my business information:

Address: 287 Wendover Ln, Building D Suite 318, Costa Mesa CA 92631
Website: copperleaf-studio.example
Phone #: (949) 555-0137
E-mail: copperleafwellness@mailbox.example

I am going to upload my logo, before and after pictures and pictures of people training on the device. Feel free to use as many/or little photos as you want.

Target Market(s)

Wealthy Adults 40+ years old looking for a personal trainer

Industry/Entity Type

Personal Trainer

Colors
0455a3
85cae6
aaaaaa
ffffff

Requirements
Must have
• At least two of the before and after photos, and two or more photos of people working out on the device.

```html
<!DOCTYPE html>
<html lang="en">
<head>
<meta charset="utf-8">
<title>Copperleaf Studio Postcard</title>
<link rel="stylesheet" href="https://fonts.googleapis.com/css2?family=Roboto+Condensed:wght@300;400;700&family=Lato:wght@400&display=swap">
<style>
  :root {
    --cyan: #40d2ec;
    --grey: #8f9c9c;
    --grey-light: #c4cbcb;
    --stamp: #5f6d71;
    --ink: #1e1e1e;
    --white: #ffffff;
    --photo-green: #4f7a3a;
    --photo-sky: #c9d3d8;
  }
  * { margin: 0; padding: 0; box-sizing: border-box; }
  html, body { width: 1200px; height: 1200px; overflow: hidden; background: var(--white); }
  .postcard {
    position: absolute;
    left: 268px;
    width: 863px;
    height: 670px;
    background: var(--white);
    transform: scale(0.8);
    transform-origin: 0 0;
    overflow: hidden;
    box-shadow: 4px 6px 10px rgba(0,0,0,0.35);
    font-family: "Lato", sans-serif;
  }
  .postcard--front { top: 48px; }
  .postcard--back { top: 620px; }
  .shapes { position: absolute; inset: 0; width: 863px; height: 670px; }
  .condensed { font-family: "Roboto Condensed", sans-serif; }

  .brand {
    position: absolute; left: 96px; top: 68px;
    display: flex; align-items: center; gap: 8px;
    font-family: "Roboto Condensed", sans-serif;
    font-weight: 700; font-size: 20px; letter-spacing: 1px;
    color: var(--grey);
  }
  .brand__dot { width: 12px; height: 12px; border-radius: 50%; background: var(--cyan); }

  .headline { position: absolute; left: 38px; top: 132px; font-family: "Roboto Condensed", sans-serif; font-weight: 700; line-height: 1; }
  .headline__main { display: block; font-size: 68px; color: var(--cyan); }
  .headline__sub { display: block; font-size: 50px; color: var(--grey); margin-top: 10px; }

  .intro {
    position: absolute; left: 40px; top: 288px; width: 302px;
    font-size: 16px; line-height: 20.5px; color: var(--ink); text-align: justify;
  }

  .offer {
    position: absolute; left: 435px; top: 58px; width: 260px;
    text-align: center; font-family: "Roboto Condensed", sans-serif; line-height: 1;
  }
  .offer__free { font-size: 44px; font-weight: 700; color: var(--cyan); }
  .offer__title { font-size: 39px; font-weight: 700; color: var(--grey); margin-top: 4px; }
  .offer__discount { font-size: 33px; font-weight: 700; color: var(--cyan); margin-top: 8px; }
  .offer__session { font-size: 33px; font-weight: 400; color: var(--grey); margin-top: 3px; }

  .front-contact { position: absolute; left: 40px; top: 568px; width: 230px; text-align: center; color: var(--white); font-family: "Roboto Condensed", sans-serif; font-weight: 700; }
  .front-contact__phone { font-size: 31px; }
  .front-contact__web { font-size: 15px; margin-top: 10px; letter-spacing: 0.3px; }

  .claim { position: absolute; left: 25px; top: 262px; font-family: "Roboto Condensed", sans-serif; line-height: 1; }
  .claim__lead { display: block; font-size: 32px; font-weight: 700; color: var(--cyan); }
  .claim__strong { display: block; font-size: 45px; font-weight: 700; color: var(--cyan); margin-top: 4px; }
  .claim__soft { display: block; font-size: 34px; font-weight: 300; color: var(--grey); margin-top: 3px; }
  .claim__big { display: block; font-size: 60px; font-weight: 700; color: var(--grey); margin-top: 0; }

  .rule { position: absolute; left: 25px; top: 446px; width: 290px; height: 2px; background: linear-gradient(to right, var(--grey-light), rgba(196,203,203,0)); }

  .contacts { position: absolute; left: 28px; top: 468px; list-style: none; font-size: 15px; color: var(--ink); }
  .contacts li { display: flex; gap: 6px; line-height: 19px; margin-bottom: 6px; }
  .contacts svg { flex: none; width: 11px; height: 11px; margin-top: 4px; }

  .stamp { position: absolute; left: 752px; top: 21px; width: 90px; height: 104px; background: var(--stamp); }
</style>
</head>
<body>

<section class="postcard postcard--front">
  <svg class="shapes" viewBox="0 0 863 670" aria-hidden="false">
    <defs>
      <linearGradient id="frontPhotoTone" x1="0" y1="0" x2="0" y2="1">
        <stop offset="0" stop-color="var(--photo-sky)"/>
        <stop offset="0.45" stop-color="#8c9a8a"/>
        <stop offset="0.6" stop-color="var(--photo-green)"/>
        <stop offset="1" stop-color="#3f6a2e"/>
      </linearGradient>
    </defs>
    <path role="img" aria-label="Photo: two women training outdoors on a rooftop lawn, one wearing a Q-Pulse suit beside the control unit"
          d="M450 225 C380 340 310 500 300 670 L863 670 L863 105 L690 105 Z" fill="url(#frontPhotoTone)"/>
    <path d="M690 92 C760 66 820 62 863 62 L863 106 C810 106 752 112 700 128 Z" fill="var(--cyan)"/>
    <path d="M0 445 C170 478 330 420 445 232 C370 360 305 520 290 670 L0 670 Z" fill="var(--cyan)"/>
    <path d="M0 492 C190 520 345 455 440 258" fill="none" stroke="var(--white)" stroke-width="10"/>
    <path d="M0 505 C195 530 350 465 438 270" fill="none" stroke="var(--grey)" stroke-width="20"/>
    <path d="M452 228 C378 350 300 510 292 670" fill="none" stroke="var(--white)" stroke-width="14"/>
    <path d="M462 222 C372 360 290 520 282 670" fill="none" stroke="var(--grey)" stroke-width="8"/>
    <path d="M455 60 A150 150 0 0 1 712 160" fill="none" stroke="var(--grey-light)" stroke-width="8"/>
    <circle cx="565" cy="150" r="132" fill="var(--white)" stroke="var(--cyan)" stroke-width="8"/>
  </svg>

  <div class="brand"><span class="brand__dot"></span>COPPERLEAF STUDIO</div>

  <h1 class="headline">
    <span class="headline__main">Lose Weight</span>
    <span class="headline__sub">Gain Muscle</span>
  </h1>

  <p class="intro">Customized Personal training using Q-Pulse, the latest technology in fitness. Reach your fitness goals in just two 25-min sessions per week</p>

  <div class="offer">
    <div class="offer__free">FREE</div>
    <div class="offer__title">Consultation</div>
    <div class="offer__discount">50% off your</div>
    <div class="offer__session">first session!</div>
  </div>

  <div class="front-contact">
    <div class="front-contact__phone">949-555-0137</div>
    <div class="front-contact__web">www.copperleaf-studio.example</div>
  </div>
</section>

<section class="postcard postcard--back">
  <svg class="shapes" viewBox="0 0 863 670">
    <defs>
      <linearGradient id="backPhotoTone" x1="0" y1="0" x2="0" y2="1">
        <stop offset="0" stop-color="#c7ccd0"/>
        <stop offset="0.55" stop-color="#aab3ba"/>
        <stop offset="1" stop-color="#f7f8fa"/>
      </linearGradient>
    </defs>
    <rect x="0" y="0" width="420" height="670" fill="#f7f8fa"/>
    <path role="img" aria-label="Photo: trainer guiding a client in a Q-Pulse suit through a floor exercise in the studio"
          d="M0 0 L362 0 C395 50 410 140 414 240 L0 240 Z" fill="url(#backPhotoTone)"/>
    <path d="M362 0 L400 0 C452 150 452 420 415 670 L190 670 C330 590 430 420 440 240 C442 150 415 70 362 0 Z" fill="var(--cyan)"/>
    <path d="M180 670 C322 588 425 420 436 240" fill="none" stroke="var(--white)" stroke-width="6"/>
    <path d="M172 670 C318 582 422 418 432 245" fill="none" stroke="var(--grey-light)" stroke-width="5"/>
    <path d="M405 0 C455 150 455 420 420 670" fill="none" stroke="var(--grey-light)" stroke-width="5"/>
  </svg>

  <h2 class="claim">
    <span class="claim__lead">up to 18 times more</span>
    <span class="claim__strong">effective than a</span>
    <span class="claim__soft">conventional gym</span>
    <span class="claim__big">workout</span>
  </h2>
  <div class="rule"></div>

  <ul class="contacts">
    <li>
      <svg viewBox="0 0 12 12"><path d="M6 0.5a3.8 3.8 0 0 0-3.8 3.8C2.2 7.2 6 11.5 6 11.5s3.8-4.3 3.8-7.2A3.8 3.8 0 0 0 6 .5zm0 5.3a1.5 1.5 0 1 1 0-3 1.5 1.5 0 0 1 0 3z" fill="var(--cyan)"/></svg>
      <span>287 Wendover Ln, Building<br>D Suite 318, Costa Mesa<br>CA 92631</span>
    </li>
    <li>
      <svg viewBox="0 0 12 12"><rect x="0.5" y="2.5" width="11" height="7" fill="var(--cyan)"/><path d="M0.5 2.5 L6 6.5 L11.5 2.5" fill="none" stroke="var(--white)" stroke-width="1"/></svg>
      <span>copperleafwellness@mailbox.example</span>
    </li>
    <li>
      <svg viewBox="0 0 12 12"><circle cx="6" cy="6" r="4.5" fill="var(--cyan)"/></svg>
      <span>copperleaf-studio.example</span>
    </li>
    <li>
      <svg viewBox="0 0 12 12"><path d="M2.5 1 L4.5 1 L5.2 3.6 L3.9 4.6 C4.6 6.2 5.8 7.4 7.4 8.1 L8.4 6.8 L11 7.5 L11 9.5 C11 10.3 10.3 11 9.5 11 C5 11 1 7 1 2.5 C1 1.7 1.7 1 2.5 1 Z" fill="var(--cyan)"/></svg>
      <span>(949) 555-0137</span>
    </li>
  </ul>

  <div class="stamp" aria-label="Stamp area"></div>
</section>

</body>
</html>
```